Brindle Yard Care. The best in the biz

I run a lawn care service that offers full service mowing. 100% satisfaction guarantee. Fast, Friendly, quality service "I am your lawns best friend" I cut residential lawns. I offer a mow package that includes trimming, edging and clean up. Prices very from 20 dollars to 75. I want my logo to stand out. Free estimates

Target Market(s)

Home owners

Industry/Entity Type

Landscaping

Contact Information for Business Card

555-812-4473 tomvale48@quillmail.net Derek. Brindle Yard care

Colors
f37122
9bcb3c
cadf82

Requirements
Must have
• Company name.
• Phone number
• Email
• My services
• images
Nice to have
• A sun that is growing grass.
Should not have
• Incorrect information

```html
<!DOCTYPE html>
<html lang="en">
<head>
<meta charset="utf-8">
<title>Brindle Yard Care – Business Card</title>
<link href="https://fonts.googleapis.com/css2?family=Open+Sans:ital,wght@0,400;0,600;0,700;1,600&display=swap" rel="stylesheet">
<style>
  :root {
    --orange: #f39024;
    --orange-deep: #ec8418;
    --green: #1f9a4a;
    --white: #ffffff;
    --paper: #f4f4f2;
    --backdrop: #e9e6e1;
    --ink-soft: #fff7ee;
  }
  * { box-sizing: border-box; margin: 0; padding: 0; }
  html, body {
    width: 1200px;
    height: 900px;
    overflow: hidden;
  }
  body {
    background: var(--backdrop);
    font-family: "Open Sans", Arial, sans-serif;
    display: flex;
    flex-direction: column;
    align-items: center;
    justify-content: center;
    gap: 30px;
  }
  .card {
    width: 700px;
    height: 400px;
    position: relative;
    overflow: hidden;
    box-shadow: 0 6px 18px rgba(0,0,0,0.18);
  }

  /* ---------- Back side ---------- */
  .card-back {
    background: var(--orange);
  }
  .card-back .brand {
    position: absolute;
    top: 58px;
    left: 250px;
    right: 40px;
    text-align: center;
    color: var(--white);
    font-weight: 700;
    font-size: 44px;
    letter-spacing: 1px;
    line-height: 1;
  }
  .card-back .promise {
    position: absolute;
    top: 170px;
    left: 250px;
    right: 40px;
    text-align: center;
    color: var(--white);
  }
  .card-back .guarantee {
    font-weight: 700;
    font-size: 22px;
  }
  .card-back .qualities {
    margin-top: 6px;
    font-weight: 600;
    font-size: 17px;
    word-spacing: 2px;
  }
  .card-back .tagline-band {
    position: absolute;
    left: 0;
    right: 0;
    top: 248px;
    height: 110px;
    background: var(--white);
    border-top: 6px solid var(--orange-deep);
  }
  .card-back .tagline {
    display: block;
    text-align: center;
    padding-top: 12px;
    color: var(--orange);
    font-style: italic;
    font-weight: 600;
    font-size: 24px;
  }

  /* ---------- Front side ---------- */
  .card-front {
    background: var(--orange);
  }
  .card-front .top-panel {
    position: absolute;
    left: 0;
    right: 0;
    top: 0;
    height: 200px;
    background: linear-gradient(180deg, var(--white), var(--paper));
    border-bottom: 7px solid var(--green);
  }
  .card-front .brand {
    position: absolute;
    top: 72px;
    left: 0;
    right: 0;
    text-align: center;
    color: var(--green);
    font-weight: 700;
    font-size: 46px;
    letter-spacing: 1px;
    line-height: 1;
  }
  .card-front .contact {
    position: absolute;
    top: 228px;
    left: 0;
    right: 0;
    text-align: center;
    color: var(--white);
  }
  .card-front .person {
    font-weight: 700;
    font-size: 22px;
    margin-bottom: 28px;
  }
  .card-front .line {
    display: flex;
    align-items: center;
    justify-content: center;
    gap: 8px;
    font-size: 16px;
    margin-bottom: 8px;
  }
  .card-front .line svg {
    width: 15px;
    height: 15px;
    flex: none;
  }
</style>
</head>
<body>

  <section class="card card-back" aria-label="Business card, back side">
    <h1 class="brand">Brindle Yard Care</h1>
    <div class="promise">
      <p class="guarantee">100% satisfaction guarantee.</p>
      <p class="qualities">Fast | Friendly | Quality Service</p>
    </div>
    <div class="tagline-band">
      <span class="tagline">I am your lawns best friend</span>
    </div>
  </section>

  <section class="card card-front" aria-label="Business card, front side">
    <div class="top-panel"></div>
    <h2 class="brand">Brindle Yard Care</h2>
    <div class="contact">
      <p class="person">Derek</p>
      <p class="line">
        <svg viewBox="0 0 24 24" aria-hidden="true"><path fill="#fff" d="M6.6 10.8a15.1 15.1 0 0 0 6.6 6.6l2.2-2.2c.3-.3.7-.4 1-.2 1.1.4 2.3.6 3.6.6.6 0 1 .4 1 1V20c0 .6-.4 1-1 1A17 17 0 0 1 3 4c0-.6.4-1 1-1h3.5c.6 0 1 .4 1 1 0 1.3.2 2.5.6 3.6.1.3 0 .7-.2 1z"/></svg>
        <span>555-812-4473</span>
      </p>
      <p class="line">
        <svg viewBox="0 0 24 24" aria-hidden="true"><rect x="2" y="5" width="20" height="14" rx="1.5" fill="#fff"/><path d="M3 6.5l9 6.5 9-6.5" fill="none" stroke="#f39024" stroke-width="1.8"/></svg>
        <span>tomvale48@quillmail.net</span>
      </p>
    </div>
  </section>

</body>
</html>
```